Heritage Hollow Business Cards

Require a business card design. <br/><br/>Needs to include logo (either round or long version) plus these details:<br/>Maya Torvell<br/>Heritage Hollow<br/>maya@kelvadtrading.com.au<br/>02 6481 7395<br/>PO Box Glenwarra NSW 2791<br/>www.heritagehollow.com.au<br/><br/>I need in an editable format so that I can create for multiple staff members. <br/><br/>

Target Market(s)

We are an online store selling renovation products to home owners are builders. Looking for a classic classy design.

Industry/Entity Type

Home And Garden

Contact Information for Business Card

Maya Torvell
Heritage Hollow
maya@kelvadtrading.com.au
02 6481 7395
PO Box Glenwarra NSW 2791
www.heritagehollow.com.au

Colors

Designer to choose colors to be used in the design.

Requirements
Must have
• Must include Logo.

```html
<!DOCTYPE html>
<html lang="en">
<head>
<meta charset="utf-8">
<title>Heritage Hollow Business Cards</title>
<link rel="stylesheet" href="https://fonts.googleapis.com/css2?family=Libre+Baskerville:wght@400;700&family=Open+Sans:wght@400&display=swap">
<style>
  :root {
    --backdrop: #1e1e1e;
    --card: #050505;
    --silver: #d4d4d4;
    --silver-soft: #9a9a9a;
    --rule: #6a6a6a;
    --icon: #7fa59a;
    --sketch-a: #1c1c1c;
    --sketch-b: #0a0a0a;
  }
  * { box-sizing: border-box; margin: 0; padding: 0; }
  html, body { width: 1200px; height: 960px; overflow: hidden; background: var(--backdrop); }
  .canvas {
    width: 1200px; height: 960px;
    display: flex; flex-direction: column; align-items: center; justify-content: center; gap: 40px;
  }
  .card {
    position: relative; width: 720px; height: 411px;
    background: var(--card); overflow: hidden;
    box-shadow: 0 14px 40px rgba(0,0,0,.55);
  }
  .brand-name {
    font-family: "Libre Baskerville", serif; font-weight: 400;
    color: var(--silver); letter-spacing: .5px;
  }
  .brand-mark { display: block; border-radius: 50%; border: 1.5px solid var(--silver); flex: none; }

  /* back of card */
  .card-back .sketch-area {
    position: absolute; inset: 0;
    background: radial-gradient(ellipse at 45% 55%, var(--sketch-a) 0%, var(--sketch-b) 70%);
  }
  .card-back .brand {
    position: absolute; left: 50%; top: 50%;
    transform: translate(-50%, -50%);
    display: flex; align-items: center; gap: 22px;
    white-space: nowrap;
  }
  .card-back .brand-mark { width: 64px; height: 64px; }
  .card-back .brand-name { font-size: 54px; }

  /* front of card */
  .card-front .brand {
    position: absolute; left: 60px; top: 95px;
    width: 220px; height: 220px;
  }
  .card-front .brand-mark { position: absolute; inset: 0; width: 220px; height: 220px; }
  .card-front .brand-name {
    position: absolute; left: 0; right: 0; top: 88px;
    font-size: 32px; text-align: center; line-height: 1.1;
  }
  .divider {
    position: absolute; left: 320px; top: 96px; width: 1px; height: 220px;
    background: var(--rule);
  }
  .contact {
    position: absolute; left: 348px; top: 98px;
    color: var(--silver); font-family: "Open Sans", sans-serif;
  }
  .person-name {
    font-family: "Libre Baskerville", serif; font-weight: 700; font-size: 22px; letter-spacing: .5px;
  }
  .person-role {
    font-family: "Libre Baskerville", serif; font-weight: 700; font-size: 13px; margin: 2px 0 12px;
    color: var(--silver-soft);
  }
  .address { font-size: 17px; line-height: 1.3; margin-bottom: 6px; }
  .contact-list { list-style: none; font-size: 17px; line-height: 1.6; }
  .contact-list li { display: flex; align-items: center; gap: 10px; white-space: nowrap; }
  .contact-list svg { width: 14px; height: 14px; flex: none; }
</style>
</head>
<body>
<main class="canvas">
  <section class="card card-back">
    <div class="sketch-area" role="img" aria-label="Faint sketched roof gable with chimney spread across the card"></div>
    <div class="brand">
      <span class="brand-mark"></span>
      <span class="brand-name">Heritage Hollow</span>
    </div>
  </section>

  <section class="card card-front">
    <div class="brand">
      <span class="brand-mark"></span>
      <span class="brand-name">Heritage<br>Hollow</span>
    </div>
    <div class="divider"></div>
    <div class="contact">
      <p class="person-name">Maya Torvell</p>
      <p class="person-role">Director</p>
      <p class="address">PO Box Glenwarra<br>NSW 2791</p>
      <ul class="contact-list">
        <li>
          <svg viewBox="0 0 24 24" aria-hidden="true"><path fill="var(--icon)" d="M6.6 10.8a15 15 0 0 0 6.6 6.6l2.2-2.2a1 1 0 0 1 1-.25 11.4 11.4 0 0 0 3.6.57 1 1 0 0 1 1 1V20a1 1 0 0 1-1 1A17 17 0 0 1 3 4a1 1 0 0 1 1-1h3.5a1 1 0 0 1 1 1c0 1.25.2 2.45.57 3.57a1 1 0 0 1-.25 1z"/></svg>
          02 6481 7395
        </li>
        <li>
          <svg viewBox="0 0 24 24" aria-hidden="true"><rect x="2" y="5" width="20" height="14" fill="var(--icon)"/><path d="M2 5l10 8 10-8" fill="none" stroke="var(--card)" stroke-width="1.6"/></svg>
          maya@kelvadtrading.com.au
        </li>
        <li>
          <svg viewBox="0 0 24 24" aria-hidden="true"><circle cx="12" cy="12" r="10" fill="var(--icon)"/><path d="M2 12h20M12 2c3 3 3 17 0 20M12 2c-3 3-3 17 0 20" fill="none" stroke="var(--card)" stroke-width="1.3"/></svg>
          www.heritagehollow.com.au
        </li>
      </ul>
    </div>
  </section>
</main>
</body>
</html>
```